Business card for medical clinic

I need an upmarket, modern medical/health business card for my clinic

Contact Information for Business Card

name, address, email, qr code

```html
<!DOCTYPE html>
<html lang="en">
<head>
<meta charset="UTF-8">
<title>Meridia Health Clinic – Business Card</title>
<link href="https://fonts.googleapis.com/css2?family=Cinzel:wght@600&family=Crimson+Text:wght@400&display=swap" rel="stylesheet">
<style>
  :root {
    --backdrop: #2b2b2b;
    --card: #f7f7f6;
    --navy: #1c3f73;
    --blue: #1f8fd0;
    --ink: #4a4a4a;
    --shadow: rgba(0,0,0,0.45);
  }
  * { margin: 0; padding: 0; box-sizing: border-box; }
  html, body {
    width: 1200px; height: 852px; overflow: hidden;
    background: var(--backdrop);
  }
  .stage {
    width: 1200px; height: 852px;
    display: flex; align-items: center; justify-content: center; gap: 60px;
  }
  .card {
    position: relative;
    width: 500px; height: 286px;
    background: var(--card);
    border-radius: 22px;
    box-shadow: 0 10px 26px var(--shadow);
    overflow: hidden;
  }
  .card--front { border-bottom: 5px solid var(--blue); }
  .brand {
    display: flex; align-items: center; gap: 14px;
    font-family: "Cinzel", serif; font-weight: 600;
    color: var(--navy); letter-spacing: 0.04em; line-height: 1;
  }
  .brand__dot {
    border-radius: 50%; background: var(--navy); flex: none;
  }
  .card--front .brand {
    position: absolute; left: 50%; top: 50%;
    transform: translate(-50%, -50%);
    font-size: 30px; white-space: nowrap;
  }
  .card--front .brand__dot { width: 22px; height: 22px; }
  .card--back .brand {
    position: absolute; left: 34px; top: 42px;
    font-size: 19px; gap: 10px; white-space: nowrap;
  }
  .card--back .brand__dot { width: 14px; height: 14px; }
  .holder {
    position: absolute; left: 34px; bottom: 36px;
  }
  .holder__name {
    font-family: "Cinzel", serif; font-weight: 600;
    font-size: 20px; color: var(--navy); letter-spacing: 0.03em;
  }
  .holder__title {
    font-family: "Crimson Text", serif; font-size: 15px; color: var(--ink);
    margin-top: -2px;
  }
  .contacts {
    position: absolute; right: 30px; top: 118px;
    list-style: none;
    font-family: "Crimson Text", serif; font-size: 14.5px; color: var(--ink);
  }
  .contacts li {
    display: flex; align-items: center; gap: 8px; height: 21px;
  }
  .contacts svg { width: 11px; height: 11px; fill: var(--navy); flex: none; }
  .contacts .address { padding-left: 19px; }
</style>
</head>
<body>
<main class="stage">
  <section class="card card--front" aria-label="Card front">
    <div class="brand"><span class="brand__dot"></span>Meridia Health Clinic</div>
  </section>

  <section class="card card--back" aria-label="Card back">
    <div class="brand"><span class="brand__dot"></span>Meridia Health Clinic</div>

    <ul class="contacts">
      <li>
        <svg viewBox="0 0 12 12" aria-hidden="true"><path d="M2.5 1h2l1 3-1.4 1a6 6 0 0 0 2.9 2.9L8 6.5l3 1v2c0 .8-.7 1.5-1.5 1.5A8.5 8.5 0 0 1 1 2.5C1 1.7 1.7 1 2.5 1z"/></svg>
        0123-456-78900
      </li>
      <li>
        <svg viewBox="0 0 12 12" aria-hidden="true"><path d="M1 2.5h10v7H1z M1.4 3 6 6.6 10.6 3" stroke="#f7f7f6" stroke-width="0.9"/></svg>
        info@meridiaclinic.com
      </li>
      <li>
        <svg viewBox="0 0 12 12" aria-hidden="true"><circle cx="6" cy="6" r="5"/><path d="M1 6h10M6 1c-2 2.5-2 7.5 0 10M6 1c2 2.5 2 7.5 0 10" stroke="#f7f7f6" stroke-width="0.7" fill="none"/></svg>
        www.meridiaclinic.com
      </li>
      <li class="address">18 Elm Row, Town, US 10452</li>
    </ul>

    <div class="holder">
      <p class="holder__name">Daniel Hale</p>
      <p class="holder__title">Managing Director</p>
    </div>
  </section>
</main>
</body>
</html>
```